Quillmarsh Property Solutions need a business card design

Hello guys. We would need a business card design asap please.
We are a start up property investment business based in London UK specialised in buying, selling, managing and letting properties and helping distressed property owners.
The name of our Business is Quillmarsh, the logo symbolises the four fundamental elements of the world (earth, air, fire and water) and so it stands for strength, stability, longevity.
We would like the business card to communicate professionalism and reliability. Many many thanks indeed for your work.

Details:

1.) Rosalind Updike
Property Investor
Mobile: +44(0)7700123456
Email: rosalind.quillmarsh@mailbox-example.com

2.) Dominic Updike
Property Investor
Mobile: +44(0)7700987654
Email: dominic.quillmarsh@mailbox-example.com

```html
<!DOCTYPE html>
<html lang="en">
<head>
<meta charset="utf-8">
<title>Quillmarsh Property Solutions – Business Card</title>
<link href="https://fonts.googleapis.com/css2?family=Montserrat:wght@600;700;800&family=Open+Sans:wght@400;600&display=swap" rel="stylesheet">
<style>
  :root {
    --brand-red: #c02c3a;
    --brand-green: #1f6b3a;
    --ink: #1d1d1d;
    --muted: #555555;
    --paper: #ffffff;
    --backdrop: #ecebe8;
    --divider: #cfcfcf;
  }
  * { box-sizing: border-box; margin: 0; padding: 0; }
  html, body {
    width: 1200px;
    height: 720px;
    overflow: hidden;
    background: var(--backdrop);
  }
  .canvas {
    position: relative;
    width: 1200px;
    height: 720px;
    display: flex;
    align-items: center;
    justify-content: center;
    gap: 40px;
  }
  .card {
    position: relative;
    width: 540px;
    height: 309px;
    overflow: hidden;
    box-shadow: 0 6px 18px rgba(0,0,0,0.15);
  }

  /* Front face */
  .card-front { background: var(--paper); }
  .card-front .swoosh {
    position: absolute;
    inset: 0;
    width: 100%;
    height: 100%;
  }
  .brand-lockup {
    position: absolute;
    left: 36px;
    top: 68px;
    width: 180px;
    text-align: center;
  }
  .brand-mark {
    display: block;
    width: 22px;
    height: 22px;
    margin: 0 auto 14px;
    background: var(--brand-red);
  }
  .brand-name {
    font-family: "Montserrat", sans-serif;
    font-weight: 800;
    font-size: 22px;
    letter-spacing: 0.5px;
    color: var(--ink);
  }
  .brand-tagline {
    font-family: "Montserrat", sans-serif;
    font-weight: 700;
    font-size: 9px;
    letter-spacing: 0.6px;
    color: var(--ink);
    margin-top: 2px;
  }
  .contact-divider {
    position: absolute;
    left: 228px;
    top: 36px;
    width: 1px;
    height: 70px;
    background: var(--divider);
  }
  .contact-list {
    position: absolute;
    left: 242px;
    top: 44px;
    list-style: none;
    font-family: "Open Sans", sans-serif;
    font-size: 12px;
    color: var(--muted);
  }
  .contact-list li {
    display: flex;
    align-items: center;
    gap: 7px;
    margin-bottom: 11px;
    white-space: nowrap;
  }
  .contact-icon { width: 11px; height: 11px; flex: none; fill: var(--muted); }
  .holder {
    position: absolute;
    right: 22px;
    top: 164px;
    text-align: right;
    color: var(--paper);
    font-family: "Open Sans", sans-serif;
  }
  .holder-name { font-weight: 600; font-size: 15px; line-height: 1.2; }
  .holder-role { font-size: 11px; margin-top: 1px; }

  /* Back face */
  .card-back {
    background: var(--brand-red);
    display: flex;
    flex-direction: column;
    justify-content: center;
    align-items: center;
    color: var(--paper);
    font-family: "Montserrat", sans-serif;
  }
  .back-name {
    font-weight: 800;
    font-size: 46px;
    letter-spacing: 1.5px;
  }
  .back-tagline {
    font-weight: 700;
    font-size: 19px;
    letter-spacing: 1.2px;
    margin-top: 2px;
  }
</style>
</head>
<body>
<main class="canvas">

  <section class="card card-front" aria-label="Business card front">
    <svg class="swoosh" viewBox="0 0 540 309" preserveAspectRatio="none" aria-hidden="true">
      <path d="M0,262 C150,250 250,140 360,128 L540,112" fill="none" stroke="var(--brand-red)" stroke-width="2"/>
      <path d="M0,274 C150,262 250,152 360,140 L540,124 L540,132 L360,148 C250,160 150,270 0,282 Z" fill="var(--brand-green)"/>
      <path d="M0,290 C150,278 250,168 360,156 L540,140 L540,309 L0,309 Z" fill="var(--brand-red)"/>
    </svg>

    <div class="brand-lockup">
      <span class="brand-mark"></span>
      <div class="brand-name">QUILLMARSH</div>
      <div class="brand-tagline">PROPERTY SOLUTIONS</div>
    </div>

    <div class="contact-divider"></div>
    <ul class="contact-list">
      <li>
        <svg class="contact-icon" viewBox="0 0 12 12"><rect x="3" y="0.5" width="6" height="11" rx="1.2"/><rect x="4" y="2" width="4" height="6" fill="#fff"/></svg>
        <span>+44(0)7700987654</span>
      </li>
      <li>
        <svg class="contact-icon" viewBox="0 0 12 12"><rect x="0.5" y="2.5" width="11" height="7.5" rx="1"/><path d="M1,3 L6,7 L11,3" fill="none" stroke="#fff" stroke-width="1"/></svg>
        <span>dominic.quillmarsh@mailbox-example.com</span>
      </li>
    </ul>

    <div class="holder">
      <div class="holder-name">Dominic Updike</div>
      <div class="holder-role">Property Investor</div>
    </div>
  </section>

  <section class="card card-back" aria-label="Business card back">
    <div class="back-name">QUILLMARSH</div>
    <div class="back-tagline">PROPERTY SOLUTIONS</div>
  </section>

</main>
</body>
</html>
```